Bespoke Builders Business Card Design

We need a business card for an established builder of high quality bespoke homes in Auckland and Northland. We build and renovate homes collaboratively facilitating effective communication between owners, builders, architects, suppliers and tradespeople. We have never built or renovated a home that leaks or has faults. We only use reliable materials. We have never been sued or had legal action taken against us. We are honest builders of bespoke homes not group mass produced homes. Our niche market is in character homes. We practice sustainability and have built a lot of coastal property. We have been in business for over thirty years . We would like to see natural colors of the environment sand,sea and maybe vegetation . The design should communicate quality, sustainability,fair pricing, open communication and the originality of bespoke building. And the fact that the builder is registered.

Industry/Entity Type

Business

Contact Information for Business Card

Rowan Tellick Builders
Ph. 021583917
18 Kestrel Rd Harwood Bay Auckland 0814
PO Box 927 Mangawhai 0583

```html
<!DOCTYPE html>
<html lang="en">
<head>
<meta charset="utf-8">
<title>Rowan Tellick Builders – Business Card</title>
<link href="https://fonts.googleapis.com/css2?family=Gelasio:wght@400&family=Open+Sans:wght@400&display=swap" rel="stylesheet">
<style>
  :root {
    --canvas-bg: #e9e7e3;
    --card-white: #ffffff;
    --ink: #1c1c1c;
    --band-light: #5d5d5d;
    --band-dark: #3a3a3a;
    --bevel: #d9d9d9;
    --contact-ink: #ffffff;
    --shadow: rgba(0, 0, 0, 0.18);
  }
  html, body {
    margin: 0;
    padding: 0;
    width: 1200px;
    height: 892px;
    overflow: hidden;
    background: var(--canvas-bg);
  }
  .canvas {
    position: relative;
    width: 1200px;
    height: 892px;
    display: flex;
    align-items: center;
    justify-content: center;
    gap: 60px;
  }
  .card {
    width: 520px;
    height: 297px;
    background: var(--card-white);
    box-shadow: 0 6px 18px var(--shadow);
    position: relative;
    overflow: hidden;
  }
  .card svg { display: block; }
  .card-front .brand-name {
    font-family: "Gelasio", "Cambria", serif;
    font-size: 33px;
    fill: var(--ink);
  }
  .card-front .rule { stroke: var(--ink); stroke-width: 1.4; }
  .card-front .contact {
    font-family: "Open Sans", "Segoe UI", sans-serif;
    font-size: 16px;
    fill: var(--contact-ink);
  }
  .card-back {
    display: flex;
    align-items: center;
    justify-content: center;
  }
  .card-back .brand-name {
    font-family: "Gelasio", "Cambria", serif;
    font-size: 38px;
    font-weight: 400;
    color: var(--ink);
    margin: 0;
  }
</style>
</head>
<body>
  <main class="canvas">
    <section class="card card-front" aria-label="Business card front">
      <svg width="520" height="297" viewBox="0 0 520 297">
        <defs>
          <linearGradient id="bandGradient" x1="0" y1="0" x2="0" y2="1">
            <stop offset="0" stop-color="var(--band-light)"/>
            <stop offset="1" stop-color="var(--band-dark)"/>
          </linearGradient>
        </defs>
        <line class="rule" x1="0" y1="88" x2="72" y2="88"/>
        <text class="brand-name" x="80" y="99">Rowan Tellick Builders</text>
        <line class="rule" x1="448" y1="88" x2="520" y2="88"/>
        <rect class="contact-band" x="0" y="118" width="520" height="179" fill="url(#bandGradient)"/>
        <polygon class="band-bevel" points="14,118 36,160 484,160 506,118" fill="var(--bevel)"/>
        <polygon class="band-notch" points="22,118 40,152 480,152 498,118" fill="var(--card-white)"/>
        <text class="contact" text-anchor="middle" x="260" y="194">021583917</text>
        <text class="contact" text-anchor="middle" x="260" y="218">18 Kestrel Rd Harwood Bay Auckland 0814</text>
        <text class="contact" text-anchor="middle" x="260" y="242">PO Box 927 Mangawhai 0583</text>
      </svg>
    </section>
    <section class="card card-back" aria-label="Business card back">
      <h1 class="brand-name">Rowan Tellick Builders</h1>
    </section>
  </main>
</body>
</html>
```